Coastline Premier Retreats Business Card Design

Design a business card for Coastline Premier Retreats. Look at the website for colors and reference. Card should have logo, name, title, office number, mobile number, email, URL and a tagline like, "Luxury Hotel & Resort Email Marketing" (This might change).

https://www.coastlinepremierretreats.example

The rest I will leave up to your imagination.

Contact Information for Business Card

Logo, name, title, office number, mobile number, email, URL and a tagline like, "Luxury Hotel & Resort Email Marketing" (This might change).

```html
<!DOCTYPE html>
<html lang="en">
<head>
<meta charset="utf-8">
<title>Coastline Premier Retreats Business Card</title>
<link href="https://fonts.googleapis.com/css2?family=Montserrat:wght@400;500;700;800&display=swap" rel="stylesheet">
<style>
  :root {
    --backdrop: #d3d6d6;
    --paper: #f7f7f5;
    --orange: #e86b12;
    --orange-deep: #d85e0c;
    --ink: #2b2b2b;
    --ink-soft: #4a4a4a;
    --white: #ffffff;
  }
  * { box-sizing: border-box; margin: 0; padding: 0; }
  html, body {
    width: 1200px; height: 829px; overflow: hidden;
    background: var(--backdrop);
    font-family: "Montserrat", Arial, sans-serif;
  }
  .stage { position: relative; width: 1200px; height: 829px; }
  .card {
    position: absolute;
    width: 500px; height: 286px;
    border-radius: 3px;
    box-shadow: 0 14px 30px rgba(0,0,0,0.18);
    overflow: hidden;
  }
  /* Front */
  .card-front { left: 70px; top: 300px; background: var(--paper); }
  .band { position: absolute; background: var(--orange-deep); }
  .band-left { left: 0; top: 46px; width: 128px; height: 40px; }
  .band-right { right: 0; top: 118px; width: 98px; height: 40px; }
  .brand-front {
    position: absolute; left: 142px; top: 58px; width: 252px;
    display: flex; align-items: center; gap: 8px;
  }
  .brand-mark { width: 12px; height: 12px; background: var(--orange); flex: none; }
  .brand-name {
    font-weight: 800; font-size: 15px; letter-spacing: 0.5px;
    color: var(--ink); line-height: 1.15; text-transform: uppercase;
  }
  .person { position: absolute; left: 34px; top: 150px; width: 190px; text-align: right; }
  .person-name {
    font-weight: 700; font-size: 20px; color: var(--orange);
    text-transform: uppercase; letter-spacing: 0.5px;
  }
  .person-title { font-size: 11px; color: var(--ink-soft); margin-top: 2px; }
  .divider { position: absolute; left: 240px; top: 146px; width: 1px; height: 66px; background: var(--orange); }
  .contacts { position: absolute; left: 254px; top: 146px; list-style: none; }
  .contacts li {
    display: flex; align-items: center; gap: 7px;
    font-size: 10px; color: var(--ink); line-height: 17px;
  }
  .contacts svg { width: 9px; height: 9px; fill: var(--orange); flex: none; }
  .address {
    position: absolute; left: 34px; bottom: 26px;
    font-size: 10.5px; color: var(--ink-soft);
  }
  .edge { position: absolute; left: 0; right: 0; bottom: 0; height: 3px; background: var(--orange); }
  /* Back */
  .card-back {
    left: 630px; top: 150px; background: var(--orange);
    display: flex; flex-direction: column; align-items: center; justify-content: center;
  }
  .brand-back {
    font-weight: 800; font-size: 26px; letter-spacing: 1px;
    color: var(--white); text-transform: uppercase; text-align: center; line-height: 1.2;
  }
  .tagline { margin-top: 22px; font-size: 11.5px; color: var(--white); letter-spacing: 0.3px; }
</style>
</head>
<body>
<main class="stage">
  <section class="card card-front" aria-label="Business card front">
    <div class="band band-left"></div>
    <div class="band band-right"></div>
    <div class="brand-front">
      <span class="brand-mark"></span>
      <span class="brand-name">Coastline Premier Retreats</span>
    </div>
    <div class="person">
      <p class="person-name">Daniel Reyes</p>
      <p class="person-title">CEO/Founder</p>
    </div>
    <div class="divider"></div>
    <ul class="contacts">
      <li><svg viewBox="0 0 10 10"><rect x="2.5" y="0" width="5" height="10" rx="1"/></svg>555.014.2200</li>
      <li><svg viewBox="0 0 10 10"><path d="M1 3 Q5 0 9 3 L8 5 L6 4 L4 4 L2 5 Z M2 6 H8 V10 H2 Z"/></svg>+34 600 000 123</li>
      <li><svg viewBox="0 0 10 10"><path d="M0 2 H10 V9 H0 Z M0 2 L5 6 L10 2" /></svg>info@coastlinepremierretreats.example</li>
      <li><svg viewBox="0 0 10 10"><circle cx="5" cy="5" r="5"/></svg>www.coastlinepremierretreats.example</li>
    </ul>
    <p class="address">Po Box, 45 B Harbor Rd North Shore, AB 10293</p>
    <div class="edge"></div>
  </section>

  <section class="card card-back" aria-label="Business card back">
    <p class="brand-back">Coastline<br>Premier Retreats</p>
    <p class="tagline">Luxury Hotel &amp; Resort Email Marketing</p>
  </section>
</main>
</body>
</html>
```